Maple Bus Card

i own a building in the bronx ny - its called "Maple 7 on 2 HDFC"i want a classy logo / business card - nothing too religuous but it is like a family there - its a large apartment building - colors i like dark red, black, medium shade of gray also reg business card stuff tel # 914-555-0173 address 4738 Larkwell Ave Bronx NY 10460 Email fijosh@aol.comslogan - " from many we are one "i can send u a picture of the building for the backside

```html
<!DOCTYPE html>
<html lang="en">
<head>
<meta charset="utf-8">
<title>Maple 7 on 2 HDFC – Business Card</title>
<link rel="stylesheet" href="https://fonts.googleapis.com/css2?family=Cinzel:wght@600&family=Montserrat:wght@700&family=Open+Sans:wght@400&display=swap">
<style>
  :root {
    --backdrop: #d9d9d9;
    --card-black: #141414;
    --gold: #f2b21b;
    --slogan-gray: #9a9a9a;
    --rule-gray: #6e6e6e;
    --white: #f2f2f2;
    --photo-brick: #7a3f34;
    --photo-leaf: #2f4a2a;
    --photo-sky: #b9c2c9;
  }
  * { box-sizing: border-box; margin: 0; padding: 0; }
  html, body {
    width: 1200px; height: 900px; overflow: hidden;
    background: var(--backdrop);
  }
  .canvas {
    position: relative; width: 1200px; height: 900px;
  }
  .card {
    position: absolute; left: 250px; width: 700px; height: 400px;
    border-radius: 26px; overflow: hidden;
    box-shadow: 0 6px 18px rgba(0,0,0,0.25);
  }
  .card--front { top: 35px; }
  .card--back { top: 465px; background: var(--card-black); }

  .building-photo {
    width: 100%; height: 100%;
    background: linear-gradient(160deg, var(--photo-sky) 0%, var(--photo-brick) 30%, var(--photo-brick) 65%, var(--photo-leaf) 100%);
  }

  .brand {
    position: absolute; left: 70px; top: 120px;
    display: flex; align-items: center; gap: 26px;
  }
  .brand__mark {
    width: 58px; height: 58px; background: var(--gold);
  }
  .brand__text { display: flex; flex-direction: column; }
  .brand__name {
    font-family: "Cinzel", serif; font-weight: 600;
    font-size: 34px; letter-spacing: 1px; color: var(--gold);
    line-height: 1.1;
  }
  .brand__rule {
    height: 1px; background: var(--rule-gray); margin: 12px 0 10px;
  }
  .brand__slogan {
    font-family: "Montserrat", sans-serif; font-weight: 700;
    font-size: 17px; letter-spacing: 1.5px; color: var(--slogan-gray);
  }

  .address {
    position: absolute; right: 40px; top: 62px; text-align: right;
    font-family: "Open Sans", sans-serif; font-size: 17px; line-height: 1.3;
    color: var(--white);
  }

  .contact {
    position: absolute; left: 70px; bottom: 40px; list-style: none;
    font-family: "Open Sans", sans-serif; font-size: 19px; color: var(--white);
  }
  .contact__item { display: flex; align-items: center; gap: 12px; line-height: 1.45; }
  .contact__icon { width: 18px; height: 18px; fill: var(--gold); flex: none; }
</style>
</head>
<body>
<main class="canvas">
  <section class="card card--front">
    <div class="building-photo" role="img" aria-label="Photograph of the brick apartment building on a tree-lined Bronx street with parked cars"></div>
  </section>

  <section class="card card--back">
    <div class="brand">
      <span class="brand__mark" aria-hidden="true"></span>
      <div class="brand__text">
        <h1 class="brand__name">Maple 7 on 2 HDFC</h1>
        <div class="brand__rule"></div>
        <p class="brand__slogan">FROM MANY WE ARE ONE</p>
      </div>
    </div>

    <address class="address">4738 Larkwell Ave<br>Bronx NY 10460</address>

    <ul class="contact">
      <li class="contact__item">
        <svg class="contact__icon" viewBox="0 0 24 24" aria-hidden="true"><path d="M3 8c0-2 2-4 9-4s9 2 9 4v2h-5V8H8v2H3z M6 12h12l2 8H4z M12 14a2.5 2.5 0 1 0 0 5a2.5 2.5 0 1 0 0-5z"/></svg>
        914-555-0173
      </li>
      <li class="contact__item">
        <svg class="contact__icon" viewBox="0 0 24 24" aria-hidden="true"><path d="M2 5h20v14H2z M3 6.5l9 6.5l9-6.5" stroke="#141414" stroke-width="1.6"/></svg>
        mavreld@quintmail.com
      </li>
    </ul>
  </section>
</main>
</body>
</html>
```